Flag Order

We were just looking to order some branding flags to put on our rental equipment for our business. We would like different examples of the colors, shapes, sizes, backgrounds etc. Was thinking of just doing the plains icon instead of the whole logo on there. but open to ideas. preferably not a white background as they could get dirty,

```html
<!DOCTYPE html>
<html lang="en">
<head>
<meta charset="utf-8">
<title>Steppe Equipment Rentals – Feather Flags</title>
<link rel="stylesheet" href="https://fonts.googleapis.com/css2?family=Lexend:wght@600&display=swap">
<style>
  :root {
    --backdrop: #555555;
    --flag-black: #1f2022;
    --flag-blue: #4a90d6;
    --sleeve: #141516;
    --photo-sky: #9cbcd8;
    --photo-sun: #d9b272;
    --photo-earth: #a38e6c;
    --white: #ffffff;
  }
  html, body {
    margin: 0;
    padding: 0;
    width: 1200px;
    height: 1200px;
    overflow: hidden;
    background: var(--backdrop);
  }
  .flag-set {
    display: block;
    width: 1200px;
    height: 1200px;
  }
  .flag-body { fill: var(--flag-black); }
  .flag-top-band { fill: var(--flag-blue); }
  .flag-sleeve { fill: none; stroke: var(--sleeve); stroke-width: 6; stroke-linecap: round; }
  .brand-name {
    font-family: "Lexend", sans-serif;
    font-weight: 600;
  }
  .brand-name--main { font-size: 46px; fill: var(--white); }
  .brand-name--sub { font-size: 11px; fill: var(--flag-blue); }
  .brand-square { fill: var(--white); }
</style>
</head>
<body>
<svg class="flag-set" viewBox="0 0 1200 1200" xmlns="http://www.w3.org/2000/svg">
  <defs>
    <linearGradient id="photo-tone" x1="0" y1="0" x2="0" y2="1">
      <stop offset="0" stop-color="var(--photo-sky)"/>
      <stop offset="0.5" stop-color="var(--photo-sun)"/>
      <stop offset="1" stop-color="var(--photo-earth)"/>
    </linearGradient>
    <clipPath id="flag-shape">
      <path d="M0,632 L0,210 Q0,8 244,0 L244,632 Z"/>
    </clipPath>
    <g id="feather-flag">
      <g clip-path="url(#flag-shape)">
        <rect class="flag-body" x="0" y="0" width="244" height="632"/>
        <rect class="flag-top-band" x="0" y="0" width="244" height="232"/>
      </g>

      <rect class="photo-area" role="img" aria-label="Excavators working at a dig site under a sunset sky"
            x="28" y="96" width="192" height="188" fill="url(#photo-tone)"/>

      <text class="brand-name brand-name--main" transform="translate(186,520) rotate(-90)"
            textLength="232" lengthAdjust="spacing">STEPPE</text>
      <text class="brand-name brand-name--sub" transform="translate(199,520) rotate(-90)"
            textLength="232" lengthAdjust="spacing">EQUIPMENT RENTALS</text>
      <rect class="brand-square" x="154" y="548" width="40" height="40"/>

      <path class="flag-sleeve" d="M0,636 L0,210 Q0,8 244,0"/>
    </g>
  </defs>

  <use href="#feather-flag" x="264" y="232"/>
  <use href="#feather-flag" x="700" y="232"/>
</svg>
</body>
</html>
```